Mira Bloom Fitness Coaching Project

I am a personal trainer based in London. My services include one-on-one PT sessions, bootcamps.
I would like the design to be minimalistic. With light colours: white, pink, purple.
I specialise in weight loss, flexibility, mobility.

Tessa Brogan
Personal Trainer
Email: tessa.brogan@quellmail.com
tel: 07700218493
Instagram: Mira Bloom

Target Market(s)

adults, mostly females (age 18-50).

Industry/Entity Type

Fitness

Contact Information for Business Card

Tessa Brogan
Personal Trainer
tel: 07700218493
Instagram: Mira Bloom

Font styles to use
Serif

Colors
eea4c8
fbd4d5
fdf9cf
cfeae6
cee9f5

Requirements
Nice to have
• minimalistic style
• easy to read and remember

```html
<!DOCTYPE html>
<html lang="en">
<head>
<meta charset="UTF-8">
<title>Tessa Brogan – Personal Trainer Business Card</title>
<link href="https://fonts.googleapis.com/css2?family=Open+Sans:wght@400;600;800&display=swap" rel="stylesheet">
<style>
  :root {
    --backdrop: #ececec;
    --card: #ffffff;
    --magenta: #c21fb5;
    --magenta-soft: rgba(194, 31, 181, 0.55);
    --text-grey: #6b6b6b;
    --photo-frame: #3a3a3a;
    --photo-warm: #b07a52;
    --photo-dark: #4a2e22;
  }
  * { box-sizing: border-box; margin: 0; padding: 0; }
  html, body {
    width: 1200px;
    height: 900px;
    overflow: hidden;
    background: var(--backdrop);
    font-family: "Open Sans", Arial, sans-serif;
  }
  .canvas {
    width: 1200px;
    height: 900px;
    display: flex;
    align-items: center;
    justify-content: center;
  }
  .business-card {
    position: relative;
    width: 900px;
    height: 514px;
    background: var(--card);
    border: 7px solid var(--magenta);
    box-shadow: 0 10px 30px rgba(0, 0, 0, 0.18);
    display: flex;
    flex-direction: column;
    align-items: center;
  }
  .portrait {
    margin-top: 64px;
    width: 140px;
    height: 118px;
    border-radius: 14px;
    border: 4px solid var(--photo-frame);
    background: radial-gradient(circle at 50% 45%, var(--photo-warm) 0%, var(--photo-dark) 80%);
  }
  .divider {
    width: 560px;
    height: 1px;
    background: linear-gradient(90deg, transparent, var(--magenta-soft) 30%, var(--magenta-soft) 70%, transparent);
  }
  .divider--top { margin-top: 8px; }
  .divider--mid { margin-top: 14px; }
  .divider--bottom { margin-top: 40px; }
  .trainer-name {
    margin-top: 6px;
    font-size: 30px;
    font-weight: 800;
    letter-spacing: 0.5px;
    color: var(--magenta);
    line-height: 1.1;
  }
  .trainer-role {
    font-size: 22px;
    font-weight: 400;
    color: var(--text-grey);
    line-height: 1.2;
  }
  .contact-line,
  .social-line,
  .services-line {
    font-size: 21px;
    color: var(--text-grey);
    line-height: 1.3;
  }
  .contact-line { margin-top: 14px; }
  .social-line {
    display: flex;
    align-items: center;
    gap: 8px;
  }
  .social-marker {
    width: 14px;
    height: 14px;
    border-radius: 3px;
    background: var(--magenta);
  }
</style>
</head>
<body>
  <main class="canvas">
    <article class="business-card">
      <div class="portrait" role="img" aria-label="Portrait photo of Tessa Brogan"></div>
      <div class="divider divider--top"></div>
      <h1 class="trainer-name">TESSA BROGAN</h1>
      <p class="trainer-role">PERSONAL TRAINER</p>
      <div class="divider divider--mid"></div>
      <p class="contact-line">(P) 07700218493 (E) tessa.brogan@quellmail.com</p>
      <p class="social-line"><span class="social-marker"></span>Mira Bloom</p>
      <p class="services-line">PT sessions, bootcamps.</p>
      <div class="divider divider--bottom"></div>
    </article>
  </main>
</body>
</html>
```